Front and content page design for Fitness Cookbook

I am looking for someone to Design a front cover for a Recipe book and also create an amazing layout for the book.

Its for a corporate seminar so has to be eye catching, professional and bold.

Content is complete

Target Market(s)

Industry/Entity Type

Health And Wellness

Font styles to use
Sans Serif

Requirements
Must have
• Eye catching, professional and bold.
• By Dorian as stated on the document
• Must have Tidewell Motion Logo on it.

```html
<!DOCTYPE html>
<html lang="en">
<head>
<meta charset="utf-8">
<title>Protein and Fat Meals</title>
<link rel="stylesheet" href="https://fonts.googleapis.com/css2?family=Oswald:wght@500&family=Roboto:wght@400;500&display=swap">
<style>
  :root {
    --page-white: #ffffff;
    --peach: #fde4cb;
    --orange: #f7941d;
    --ink: #3a3a3a;
  }
  html, body {
    margin: 0;
    padding: 0;
    overflow: hidden;
  }
  .page {
    position: relative;
    width: 849px;
    height: 1200px;
    background: var(--page-white);
    overflow: hidden;
    font-family: "Roboto", Arial, sans-serif;
    color: var(--ink);
  }
  .content-band {
    position: absolute;
    left: 0;
    top: 472px;
    width: 100%;
    height: 728px;
    background: var(--peach);
  }
  .chapter-title {
    position: absolute;
    left: 98px;
    top: 414px;
    margin: 0;
    font-family: "Oswald", "Arial Narrow", sans-serif;
    font-weight: 500;
    font-size: 60px;
    line-height: 60px;
    letter-spacing: -0.5px;
    color: var(--orange);
    text-transform: uppercase;
  }
  .body-copy {
    position: absolute;
    left: 98px;
    top: 552px;
    width: 680px;
  }
  .section + .section {
    margin-top: 16px;
  }
  .section-heading {
    margin: 0 0 4px;
    font-weight: 500;
    font-size: 22px;
    line-height: 30px;
  }
  .point-list {
    list-style: none;
    margin: 0;
    padding: 0;
    font-size: 13px;
    line-height: 25px;
  }
  .point-list li::before {
    content: "- ";
  }
</style>
</head>
<body>
  <main class="page">
    <div class="content-band"></div>
    <h1 class="chapter-title">Protein and<br>Fat Meals</h1>

    <div class="body-copy">
      <section class="section">
        <h2 class="section-heading">Best used:</h2>
        <ul class="point-list">
          <li>Anytime of the day other than around training (goal dependent)</li>
          <li>Rest days</li>
          <li>Breakfasts (especially meals containing red meat)</li>
          <li>During a low carb or ‘reset’ plan/phase</li>
        </ul>
      </section>

      <section class="section">
        <h2 class="section-heading">Why eat these meals:</h2>
        <ul class="point-list">
          <li>To help regulate blood sugar levels throughout the day</li>
          <li>To ‘teach’ your body to use fats as fuel, resulting in greater fat loss long term</li>
          <li>To keep you fuller for longer</li>
          <li>To help ‘clean out’ your digestive system and liver pathways</li>
          <li>Increase mental focus and awareness</li>
        </ul>
      </section>
    </div>
  </main>
</body>
</html>
```